Business card for medical clinic

I need an upmarket, modern medical/health business card for my clinic

Contact Information for Business Card

name, address, email, qr code

```html
<!DOCTYPE html>
<html lang="en">
<head>
<meta charset="utf-8">
<title>Meridian Wellness Group – Business Card</title>
<link rel="stylesheet" href="https://fonts.googleapis.com/css2?family=Montserrat:wght@400;500;600;700&display=swap">
<style>
  :root {
    --backdrop: #3a3129;
    --card: #1e2a47;
    --card-shadow: rgba(0, 0, 0, 0.55);
    --accent: #2ea6e2;
    --brand-teal: #2f8fb8;
    --text-light: #e9edf5;
    --emboss: #2f4582;
  }
  * { margin: 0; padding: 0; box-sizing: border-box; }
  html, body {
    width: 900px;
    height: 1200px;
    overflow: hidden;
    background: var(--backdrop);
    font-family: "Montserrat", Arial, sans-serif;
  }
  .card {
    position: absolute;
    left: 80px;
    width: 742px;
    height: 442px;
    background: var(--card);
    border-radius: 28px;
    box-shadow: 0 10px 22px var(--card-shadow);
    overflow: hidden;
  }
  .card--front { top: 130px; }
  .card--back { top: 637px; }

  .brand-name {
    position: absolute;
    left: 35px;
    top: 68px;
    font-size: 27px;
    font-weight: 600;
    letter-spacing: 1.5px;
    color: var(--brand-teal);
    text-transform: uppercase;
  }
  .person { position: absolute; left: 39px; top: 186px; }
  .person__name {
    font-size: 25px;
    font-weight: 700;
    color: var(--accent);
    line-height: 1.1;
  }
  .person__title {
    margin-top: 6px;
    font-size: 15px;
    font-weight: 500;
    color: var(--text-light);
  }
  .address {
    position: absolute;
    left: 41px;
    top: 262px;
    font-size: 16px;
    line-height: 20px;
    color: var(--text-light);
    font-style: normal;
  }
  .contact-list {
    position: absolute;
    left: 41px;
    top: 325px;
    list-style: none;
  }
  .contact-list li {
    display: flex;
    align-items: center;
    height: 31px;
    font-size: 15px;
    color: var(--text-light);
  }
  .contact-list svg {
    width: 15px;
    height: 15px;
    margin-right: 12px;
    fill: var(--accent);
  }

  .back-brand {
    position: absolute;
    left: 0;
    right: 0;
    top: 190px;
    display: flex;
    align-items: center;
    justify-content: center;
    gap: 18px;
  }
  .back-brand__mark {
    width: 46px;
    height: 46px;
    border-radius: 50%;
    border: 4px solid var(--emboss);
  }
  .back-brand__name {
    font-size: 34px;
    font-weight: 600;
    letter-spacing: 2px;
    color: var(--emboss);
    text-transform: uppercase;
  }
</style>
</head>
<body>
  <section class="card card--front">
    <div class="brand-name">Meridian Wellness Group</div>

    <div class="person">
      <div class="person__name">Daniel Reyes</div>
      <div class="person__title">Managing Director</div>
    </div>

    <address class="address">
      240 Cedar Hollow Road<br>
      Ridgeland, MS 39157
    </address>

    <ul class="contact-list">
      <li>
        <svg viewBox="0 0 24 24" aria-hidden="true"><path d="M6.6 10.8a15.1 15.1 0 0 0 6.6 6.6l2.2-2.2a1 1 0 0 1 1-.25 11.4 11.4 0 0 0 3.6.57 1 1 0 0 1 1 1V20a1 1 0 0 1-1 1A17 17 0 0 1 3 4a1 1 0 0 1 1-1h3.5a1 1 0 0 1 1 1c0 1.25.2 2.45.57 3.57a1 1 0 0 1-.25 1z"/></svg>
        555.214.7730
      </li>
      <li>
        <svg viewBox="0 0 24 24" aria-hidden="true"><path d="M2 5h20v2l-10 6L2 7z"/><path d="M2 9l10 6 10-6v10H2z"/></svg>
        hello@meridianwellness.com
      </li>
      <li>
        <svg viewBox="0 0 24 24" aria-hidden="true"><path d="M12 2a10 10 0 1 0 0 20 10 10 0 0 0 0-20zm6.9 6h-3a15.6 15.6 0 0 0-1.3-4A8 8 0 0 1 18.9 8zM12 4c.8 1.2 1.5 2.5 1.9 4h-3.8c.4-1.5 1.1-2.8 1.9-4zM4.3 14a8 8 0 0 1 0-4h3.3a16 16 0 0 0 0 4zm.8 2h3a15.6 15.6 0 0 0 1.3 4A8 8 0 0 1 5.1 16zm3-8h-3a8 8 0 0 1 4.3-4 15.6 15.6 0 0 0-1.3 4zM12 20c-.8-1.2-1.5-2.5-1.9-4h3.8c-.4 1.5-1.1 2.8-1.9 4zm2.3-6H9.7a14.6 14.6 0 0 1 0-4h4.6a14.6 14.6 0 0 1 0 4zm.3 6a15.6 15.6 0 0 0 1.3-4h3a8 8 0 0 1-4.3 4zm1.8-6a16 16 0 0 0 0-4h3.3a8 8 0 0 1 0 4z"/></svg>
        www.meridianwellness.com
      </li>
    </ul>
  </section>

  <section class="card card--back">
    <div class="back-brand">
      <span class="back-brand__mark"></span>
      <span class="back-brand__name">Meridian Wellness Group</span>
    </div>
  </section>
</body>
</html>
```